business card for a massage therapy practice named 'Cedar and Willow Massage Studio'

I really need a trendy, yet easy on the eyes business card to complement my logo. Ideally with some gold or rose gold foil work.

My uploaded file of the logo I have in horizontal but I have a vertical version as well. Another color that is used in the website is a blush pink here and there. I'd like to see some trendy tropical leaves in the design.

```html
<!DOCTYPE html>
<html lang="en">
<head>
<meta charset="utf-8">
<title>Cedar and Willow Massage Studio – Business Card</title>
<link href="https://fonts.googleapis.com/css2?family=Dancing+Script:wght@600&family=Work+Sans:wght@400;500&display=swap" rel="stylesheet">
<style>
  :root {
    --backdrop: #1f1f21;
    --card-stock: #f3f2ee;
    --rose-gold: #c7826f;
    --rose-gold-soft: #d39a89;
    --shadow: rgba(0, 0, 0, 0.45);
  }
  * { box-sizing: border-box; margin: 0; padding: 0; }
  html, body { width: 1200px; height: 900px; overflow: hidden; }
  body {
    background: var(--backdrop);
    font-family: "Work Sans", Arial, sans-serif;
    color: var(--rose-gold);
    position: relative;
  }
  .card {
    position: absolute;
    left: 250px;
    width: 700px;
    height: 400px;
    background: var(--card-stock);
    box-shadow: 0 18px 40px var(--shadow);
  }
  .card--front { top: 30px; }
  .card--back { top: 470px; }

  .brand {
    display: flex;
    align-items: center;
    gap: 14px;
  }
  .brand__dot {
    width: 22px;
    height: 22px;
    border-radius: 50%;
    background: var(--rose-gold);
    flex: none;
  }
  .brand__name {
    font-family: "Work Sans", Arial, sans-serif;
    font-weight: 500;
    color: var(--rose-gold);
    text-transform: uppercase;
    letter-spacing: 0.14em;
    line-height: 1.35;
  }

  .card--front .brand {
    position: absolute;
    left: 50%;
    top: 50%;
    transform: translate(-50%, -50%);
  }
  .card--front .brand__name { font-size: 26px; }

  .card--back .brand {
    position: absolute;
    left: 48px;
    top: 150px;
    width: 280px;
  }
  .card--back .brand__name { font-size: 17px; }

  .divider {
    position: absolute;
    left: 348px;
    top: 115px;
    width: 2px;
    height: 170px;
    background: var(--rose-gold);
  }

  .contact {
    position: absolute;
    left: 378px;
    top: 112px;
    width: 300px;
  }
  .contact__person {
    font-family: "Dancing Script", cursive;
    font-weight: 600;
    font-size: 31px;
    letter-spacing: 0.03em;
    color: var(--rose-gold);
    margin-bottom: 10px;
  }
  .contact__address {
    font-size: 14px;
    line-height: 1.4;
    color: var(--rose-gold-soft);
    margin-bottom: 14px;
  }
  .contact__list { list-style: none; }
  .contact__item {
    display: flex;
    align-items: center;
    gap: 9px;
    font-size: 16px;
    line-height: 1.45;
  }
  .contact__icon { width: 11px; height: 11px; flex: none; }
</style>
</head>
<body>
  <section class="card card--front" aria-label="Card front">
    <div class="brand">
      <span class="brand__dot"></span>
      <span class="brand__name">Cedar and Willow<br>Massage Studio</span>
    </div>
  </section>

  <section class="card card--back" aria-label="Card back">
    <div class="brand">
      <span class="brand__dot"></span>
      <span class="brand__name">Cedar and Willow<br>Massage Studio</span>
    </div>

    <div class="divider"></div>

    <div class="contact">
      <p class="contact__person">Marisol Bennett</p>
      <p class="contact__address">418 Linden Ave. suite 210,<br>Fairview, CA 95012</p>
      <ul class="contact__list">
        <li class="contact__item">
          <svg class="contact__icon" viewBox="0 0 12 12" aria-hidden="true">
            <path d="M2.5 1 L4.5 1 L5.2 3.6 L4 4.6 Q5.2 7 7.4 8 L8.4 6.8 L11 7.5 L11 9.5 Q10.5 11 9 11 Q1 10 1 2.6 Q1 1 2.5 1 Z" fill="var(--rose-gold)"/>
          </svg>
          (555) 214-7730
        </li>
        <li class="contact__item">
          <svg class="contact__icon" viewBox="0 0 12 12" aria-hidden="true">
            <rect x="0.8" y="2.2" width="10.4" height="7.6" fill="none" stroke="var(--rose-gold)" stroke-width="1.2"/>
            <path d="M0.8 2.4 L6 6.4 L11.2 2.4" fill="none" stroke="var(--rose-gold)" stroke-width="1.2"/>
          </svg>
          hello@cedarandwillow.com
        </li>
        <li class="contact__item">
          <svg class="contact__icon" viewBox="0 0 12 12" aria-hidden="true">
            <circle cx="6" cy="6" r="5" fill="none" stroke="var(--rose-gold)" stroke-width="1.1"/>
            <ellipse cx="6" cy="6" rx="2.2" ry="5" fill="none" stroke="var(--rose-gold)" stroke-width="1"/>
            <line x1="1" y1="6" x2="11" y2="6" stroke="var(--rose-gold)" stroke-width="1"/>
          </svg>
          www.cedarandwillow.com
        </li>
      </ul>
    </div>
  </section>
</body>
</html>
```